professional business card design for technology company

We are a small technology consulting firm, specialising in consulting based around Cloud and Managed services. Our colour scheme is yellow, blue and white, as you can see in the logos. Although we are based in melbourne australia, due to the nature of our work, our clients can be located anywhere. We are looking for a clean, professional, positive look - similar to our company logo

Target Market(s)

small business

Industry/Entity Type

Business

Contact Information for Business Card

eye catching, designed to incorporate some level of raised printing. Must contain website address, phone number, name and job title

Requirements
Must have
• Logo (attached) - use of the same colour scheme

```html
<!DOCTYPE html>
<html lang="en">
<head>
<meta charset="utf-8">
<title>Nimbara business card</title>
<link rel="stylesheet" href="https://fonts.googleapis.com/css2?family=Open+Sans:wght@400;600;700&display=swap">
<style>
  :root {
    --backdrop: #dfe2e6;
    --charcoal: #5e5e60;
    --ink: #2f2f31;
    --sky: #3aaee4;
    --paper: #f4f4f4;
    --paper-shade: #d9d9d9;
    --white: #ffffff;
  }
  html, body {
    margin: 0;
    width: 1200px;
    height: 866px;
    overflow: hidden;
    background: var(--backdrop);
    font-family: "Open Sans", Arial, sans-serif;
  }
  .canvas {
    position: relative;
    width: 1200px;
    height: 866px;
  }
  .card {
    position: absolute;
    top: 278px;
    width: 540px;
    height: 309px;
    overflow: hidden;
    box-shadow: 0 10px 26px rgba(0, 0, 0, 0.18);
  }
  .card-back {
    left: 40px;
    background: var(--charcoal);
    display: flex;
    align-items: center;
    justify-content: center;
    gap: 14px;
  }
  .card-back .brand-dot {
    width: 22px;
    height: 22px;
    border-radius: 50%;
    background: var(--white);
  }
  .card-back .brand-name {
    color: var(--white);
    font-weight: 700;
    font-size: 46px;
    letter-spacing: -0.5px;
  }
  .card-front {
    left: 620px;
    background: radial-gradient(ellipse at 55% 45%, var(--white) 0%, var(--paper) 45%, var(--paper-shade) 100%);
  }
  .card-front .swoosh {
    position: absolute;
    inset: 0;
    width: 540px;
    height: 309px;
  }
  .brand {
    position: absolute;
    left: 30px;
    top: 118px;
    display: flex;
    align-items: center;
    gap: 10px;
  }
  .brand .brand-dot {
    width: 16px;
    height: 16px;
    border-radius: 50%;
    background: var(--sky);
  }
  .brand .brand-name {
    color: var(--charcoal);
    font-weight: 700;
    font-size: 40px;
    letter-spacing: -0.5px;
    line-height: 1;
  }
  .person {
    position: absolute;
    left: 32px;
    top: 188px;
  }
  .person-name {
    margin: 0;
    color: var(--sky);
    font-weight: 700;
    font-size: 15px;
  }
  .person-title {
    margin: 2px 0 0;
    color: var(--ink);
    font-size: 14px;
  }
  .contact {
    position: absolute;
    right: 16px;
    top: 172px;
    margin: 0;
    padding: 0;
    list-style: none;
    text-align: right;
    color: var(--white);
    font-size: 11px;
    line-height: 16px;
  }
  .contact li {
    display: flex;
    justify-content: flex-end;
    align-items: center;
    gap: 5px;
  }
  .contact svg {
    width: 9px;
    height: 9px;
    fill: var(--white);
  }
</style>
</head>
<body>
<main class="canvas">

  <section class="card card-back" aria-label="Card back">
    <span class="brand-dot"></span>
    <span class="brand-name">Nimbara</span>
  </section>

  <section class="card card-front" aria-label="Card front">
    <svg class="swoosh" viewBox="0 0 540 309" aria-hidden="true">
      <path d="M512 0 C455 70 430 215 140 309 L540 309 L540 0 Z" fill="var(--charcoal)"/>
      <path d="M498 0 C445 55 430 170 150 240 C330 210 430 140 512 0 Z" fill="var(--sky)"/>
      <path d="M0 255 C120 270 250 265 360 222 C300 260 180 298 0 288 Z" fill="var(--sky)"/>
      <path d="M0 288 C180 298 300 260 360 222 C320 270 200 312 0 309 Z" fill="var(--paper-shade)"/>
    </svg>

    <div class="brand">
      <span class="brand-dot"></span>
      <span class="brand-name">Nimbara</span>
    </div>

    <div class="person">
      <p class="person-name">Maren Holt-Vance</p>
      <p class="person-title">Consultant</p>
    </div>

    <ul class="contact">
      <li>210, 9th floor, Quay</li>
      <li>Harbour Lane VIC</li>
      <li>013 572 4680
        <svg viewBox="0 0 10 10" aria-hidden="true"><path d="M2 0 L4 2.5 L3 3.8 C3.8 5.5 4.6 6.3 6.2 7 L7.5 6 L10 8 L8.5 10 C4 9.5 0.5 6 0 1.5 Z"/></svg>
      </li>
      <li>013 572 4681
        <svg viewBox="0 0 10 10" aria-hidden="true"><rect x="1" y="3" width="8" height="6"/><rect x="3" y="0" width="4" height="3"/></svg>
      </li>
      <li>hello@nimbara.net
        <svg viewBox="0 0 10 10" aria-hidden="true"><path d="M0 2 H10 V8 H0 Z M0 2 L5 6 L10 2" stroke="var(--charcoal)" stroke-width="0.8"/></svg>
      </li>
      <li>www.nimbaracloud.net</li>
    </ul>
  </section>

</main>
</body>
</html>
```